Northfield Builders Guild Business card

We are looking for a new business card design with photo included.
Our business is a nonprofit construction contractor membership organization. We offer business education, assist with business setup and licensing, provide safety training, and provide a member directory.
URL: www.builderslinkguild.org
Color code:
CMYK: 0 cyan, 42 magenta, 100 yellow, 0 black for Print.
Hexidecimal: #FF9900
RGB: R 255; G 153; B 0

```html
<!DOCTYPE html>
<html lang="en">
<head>
<meta charset="utf-8">
<title>Northfield Builders Guild – Business Card</title>
<link href="https://fonts.googleapis.com/css2?family=Jost:wght@400;500;700&display=swap" rel="stylesheet">
<style>
  :root {
    --page-bg: #2a2a2c;
    --card-bg: #1c1d1f;
    --card-bg-deep: #141517;
    --pattern-light: #2c2d30;
    --brand-orange: #ff9900;
    --text-white: #ffffff;
    --rule-grey: #5a5b5e;
  }
  * { margin: 0; padding: 0; box-sizing: border-box; }
  html, body {
    width: 1200px; height: 1108px; overflow: hidden;
    background: var(--page-bg);
    font-family: "Jost", Arial, sans-serif;
  }
  .card-stage {
    position: relative; width: 1200px; height: 1108px;
    display: flex; justify-content: center; align-items: center; gap: 60px;
  }
  .card {
    width: 420px; height: 700px; border-radius: 26px;
    background: var(--card-bg);
    box-shadow: 0 18px 40px rgba(0,0,0,.45);
    position: relative; overflow: hidden;
  }
  .card-front {
    display: flex; flex-direction: column; align-items: center;
    text-align: center; color: var(--text-white);
    padding: 110px 36px 0;
  }
  .brand-name {
    display: flex; align-items: center; gap: 12px;
    font-weight: 700; font-size: 30px; line-height: 1.05;
    color: var(--brand-orange); text-transform: uppercase;
    letter-spacing: 0.5px;
  }
  .brand-dot {
    width: 22px; height: 22px; border-radius: 50%;
    background: var(--brand-orange); flex-shrink: 0;
  }
  .person { margin-top: 120px; }
  .person-name { font-weight: 700; font-size: 28px; letter-spacing: 0.5px; text-transform: uppercase; }
  .person-role { font-weight: 400; font-size: 20px; color: var(--brand-orange); text-transform: uppercase; margin-top: 2px; }
  .icon-row {
    display: flex; align-items: center; gap: 6px; margin: 14px 0 12px;
    width: 100%; justify-content: center;
  }
  .icon-row .rule { flex: 1; height: 1px; background: var(--rule-grey); max-width: 60px; }
  .contact-icon { width: 30px; height: 30px; }
  .contact-list { list-style: none; font-size: 20px; line-height: 1.45; font-weight: 400; }
  .contact-list .accent { color: var(--brand-orange); }
  .divider { width: 210px; height: 1px; background: var(--rule-grey); margin: 14px 0 10px; }
  .address { font-size: 20px; line-height: 1.35; }
  .card-back {
    background: linear-gradient(200deg, var(--pattern-light) 0%, var(--card-bg) 45%, var(--card-bg-deep) 100%);
  }
  .back-mark {
    position: absolute; left: 50%; top: 58%; transform: translate(-50%, -50%);
    width: 64px; height: 64px; border-radius: 50%; background: var(--brand-orange);
  }
</style>
</head>
<body>
<main class="card-stage">
  <section class="card card-front" aria-label="Card front">
    <div class="brand-name"><span class="brand-dot"></span><span>Northfield<br>Builders Guild</span></div>

    <div class="person">
      <h1 class="person-name">Daniel Reyes</h1>
      <p class="person-role">Managing Director</p>
    </div>

    <div class="icon-row">
      <span class="rule"></span>
      <svg class="contact-icon" viewBox="0 0 30 30" aria-label="Phone"><circle cx="15" cy="15" r="14" fill="#ff9900"/><path d="M10 8c1-1 2 0 3 2s0 2-1 3c1 2 3 4 5 5 1-1 1-2 3-1s3 2 2 3-3 2-5 1-7-5-8-8 0-4 1-5z" fill="#1c1d1f"/></svg>
      <svg class="contact-icon" viewBox="0 0 30 30" aria-label="Mobile"><circle cx="15" cy="15" r="14" fill="#ff9900"/><rect x="10.5" y="7" width="9" height="16" rx="1.5" fill="none" stroke="#1c1d1f" stroke-width="2"/><circle cx="15" cy="20" r="1" fill="#1c1d1f"/></svg>
      <svg class="contact-icon" viewBox="0 0 30 30" aria-label="Fax"><circle cx="15" cy="15" r="14" fill="#ff9900"/><rect x="11" y="7" width="8" height="5" fill="#1c1d1f"/><rect x="7.5" y="12" width="15" height="7" rx="1" fill="#1c1d1f"/><rect x="11" y="17" width="8" height="6" fill="#1c1d1f" stroke="#ff9900" stroke-width="1"/></svg>
      <svg class="contact-icon" viewBox="0 0 30 30" aria-label="Email"><circle cx="15" cy="15" r="14" fill="#ff9900"/><rect x="7.5" y="10" width="15" height="10" fill="#1c1d1f"/><path d="M7.5 10l7.5 6 7.5-6" fill="none" stroke="#ff9900" stroke-width="1.3"/></svg>
      <svg class="contact-icon" viewBox="0 0 30 30" aria-label="Website"><circle cx="15" cy="15" r="14" fill="#ff9900"/><g fill="none" stroke="#1c1d1f" stroke-width="1.5"><circle cx="15" cy="15" r="7.5"/><ellipse cx="15" cy="15" rx="3.5" ry="7.5"/><path d="M7.5 15h15M9 11h12M9 19h12"/></g></svg>
      <span class="rule"></span>
    </div>

    <ul class="contact-list">
      <li>(555) 201-4830 (Office)</li>
      <li>800-555-0142</li>
      <li>555.310.7264</li>
      <li>support@nbguild.org</li>
      <li>www.<span class="accent">builderslinkguild</span>.org</li>
    </ul>

    <div class="divider"></div>
    <address class="address" style="font-style:normal">2400 NW Elm Ridge Rd<br>Suite #210, Fairview, OR 97000</address>
  </section>

  <section class="card card-back" role="img" aria-label="Card back: dark tonal repeating brand pattern with a small orange brand mark">
    <span class="back-mark"></span>
  </section>
</main>
</body>
</html>
```